Business Card Design

I already have a company logo for my company. I have a logo for the manufacturer we represent. I want a professional business card design.

```html
<!DOCTYPE html>
<html lang="en">
<head>
<meta charset="utf-8">
<title>Beacon Signal Co. — Business Card</title>
<link rel="stylesheet" href="https://fonts.googleapis.com/css2?family=Montserrat:wght@400;500;600;700&display=swap">
<style>
  :root {
    --page-bg: #e9e7e4;
    --card-white: #ffffff;
    --card-black: #1b1b1c;
    --card-black-hi: #3a3a3c;
    --brand-red: #e8343f;
    --brand-grey: #8f9093;
    --ink: #2a2a2a;
    --ink-soft: #555555;
  }
  * { box-sizing: border-box; margin: 0; padding: 0; }
  html, body {
    width: 1200px; height: 913px; overflow: hidden;
    background: var(--page-bg);
    font-family: "Montserrat", Arial, sans-serif;
  }
  .sheet {
    position: relative; width: 1200px; height: 913px;
  }
  .card {
    position: absolute; left: 250px; width: 700px; height: 400px;
    box-shadow: 0 6px 18px rgba(0,0,0,0.18);
  }
  .card--front {
    top: 36px;
    background: linear-gradient(135deg, var(--card-black-hi) 0%, var(--card-black) 55%, #111112 100%);
    display: flex; align-items: center; justify-content: center;
  }
  .card--back {
    top: 476px;
    background: var(--card-white);
  }
  .brand {
    display: flex; align-items: center; gap: 14px;
  }
  .brand__mark {
    width: 30px; height: 30px; background: var(--brand-red);
  }
  .brand__name {
    font-weight: 700; text-transform: uppercase; letter-spacing: 1px;
  }
  .card--front .brand__name { color: var(--brand-grey); font-size: 34px; }
  .card--back .brand {
    position: absolute; top: 34px; right: 38px; gap: 10px;
  }
  .card--back .brand__mark { width: 20px; height: 20px; }
  .card--back .brand__name { color: var(--brand-red); font-size: 20px; }
  .person {
    position: absolute; left: 44px; top: 150px;
  }
  .person__name {
    color: var(--brand-red); font-weight: 600; font-size: 27px;
  }
  .person__title {
    color: var(--ink); font-size: 15px; margin-top: 4px;
  }
  .address {
    position: absolute; right: 44px; top: 150px;
    text-align: right; color: var(--ink); font-size: 15px; line-height: 1.45;
  }
  .contacts {
    position: absolute; left: 44px; bottom: 36px;
    list-style: none; color: var(--ink-soft); font-size: 15px;
  }
  .contacts li {
    display: flex; align-items: center; gap: 12px; line-height: 1.6;
  }
  .contacts svg { width: 13px; height: 13px; fill: var(--brand-red); flex: none; }
</style>
</head>
<body>
<main class="sheet">
  <section class="card card--front" aria-label="Card front">
    <div class="brand">
      <span class="brand__mark"></span>
      <span class="brand__name">Beacon Signal Co.</span>
    </div>
  </section>

  <section class="card card--back" aria-label="Card back">
    <div class="brand">
      <span class="brand__mark"></span>
      <span class="brand__name">Beacon Signal Co.</span>
    </div>

    <div class="person">
      <p class="person__name">Daniel Reyes</p>
      <p class="person__title">Managing Director</p>
    </div>

    <address class="address" style="font-style: normal;">
      2240 Alder Ave<br>
      Fairmont, CO 80000
    </address>

    <ul class="contacts">
      <li>
        <svg viewBox="0 0 16 16" aria-hidden="true"><path d="M3 1h3l1.5 4-2 1.3a9 9 0 0 0 4.2 4.2L11 8.5l4 1.5v3a2 2 0 0 1-2 2A13 13 0 0 1 1 3a2 2 0 0 1 2-2z"/></svg>
        555.210.0147
      </li>
      <li>
        <svg viewBox="0 0 16 16" aria-hidden="true"><path d="M1 3h14v10H1z M1 3l7 6 7-6" stroke="#fff" stroke-width="1.2"/></svg>
        info@beaconsignalco.com
      </li>
      <li>
        <svg viewBox="0 0 16 16" aria-hidden="true"><circle cx="8" cy="8" r="7"/><path d="M1 8h14M8 1c-3 3-3 11 0 14M8 1c3 3 3 11 0 14" stroke="#fff" stroke-width="1" fill="none"/></svg>
        www.beaconsignalco.com
      </li>
    </ul>
  </section>
</main>
</body>
</html>
```